Fresh, modern, fun business card for pediatric dental practice

Need a business card for fresh, modern, fun pediatric dental practice

Clean look that matches our website's font and colors

We prefer the look of curved corners on business cards

Target Market(s)

parents (mothers) of young children, professionals, mid-high class

Industry/Entity Type

Dental

Contact Information for Business Card

Maplebrook Pediatric Dentistry
482 Quarry Lane
Suite 517
Fernhollow, PA 17521
717.555.0193
www.maplebrookkidsdental.example

Mei-Ran Tsai, DMD
Corinne Walbeck, DMD
(we are working on our email address, but we would like that on the card as well)

Font styles to use
Sans Serif

Requirements
Must have
• All info; we would also like to make cards for individual staff members
• colors from our website and color palatte, attatched
• use same font and design as website for branding
Nice to have
• clean, simple card that has a pop of color
• we would like to see a few designs with our tag line "where smiles get brighter"
• we are not sure if we want to have it on there or not
• we would like to see a few designs incorporating the ribbon graphic on our website where the word WELCOME is

```html
<!DOCTYPE html>
<html lang="en">
<head>
<meta charset="utf-8">
<title>Maplebrook Pediatric Dentistry – Business Card</title>
<link rel="stylesheet" href="https://fonts.googleapis.com/css2?family=Raleway:wght@500;600&family=Ubuntu:wght@400;500&display=swap">
<style>
  :root {
    --sun: #f5b82e;
    --sun-soft: #fbe3a6;
    --berry: #c2188a;
    --card: #ffffff;
    --backdrop: #ebe8e4;
  }
  * { margin: 0; padding: 0; box-sizing: border-box; }
  html, body { width: 1200px; height: 900px; overflow: hidden; }
  body { background: var(--backdrop); position: relative; font-family: "Ubuntu", sans-serif; }

  .card {
    position: absolute;
    background: var(--card);
    border-radius: 18px;
    overflow: hidden;
    box-shadow: 0 6px 18px rgba(0,0,0,0.12);
  }
  .card--front { left: 78px; top: 35px; width: 588px; height: 362px; }
  .card--back { left: 390px; top: 507px; width: 565px; height: 348px; }

  .front__accent {
    position: absolute; left: -70px; top: 70px;
    width: 230px; height: 230px; border-radius: 50%;
    background: var(--sun-soft);
  }

  .doctors {
    position: absolute; right: 36px; top: 28px; text-align: right;
    font-family: "Raleway", sans-serif; font-weight: 500; font-size: 21px; line-height: 25px;
  }
  .doctors .given { color: var(--sun); }
  .doctors .family { color: var(--berry); }
  .doctors .degree { color: var(--berry); font-size: 17px; }

  .practice {
    position: absolute; right: 38px; top: 133px; text-align: right; color: var(--berry);
  }
  .practice__name { font-size: 18px; font-weight: 500; line-height: 26px; }
  .practice__address { font-size: 16px; line-height: 25px; }

  .contacts {
    position: absolute; right: 38px; top: 236px; list-style: none; text-align: right;
    color: var(--berry); font-size: 15px; line-height: 24.5px;
  }
  .contacts li { display: flex; justify-content: flex-end; align-items: center; gap: 12px; }
  .contacts svg { width: 12px; height: 12px; flex: none; }
  .icon-fill { fill: var(--sun); }
  .icon-mail rect { fill: var(--sun); }
  .icon-mail path { fill: none; stroke: var(--card); stroke-width: 2; }

  .brand {
    position: absolute; left: 0; right: 0; top: 92px; text-align: center; color: var(--berry);
    font-weight: 500;
  }
  .brand__mark {
    width: 58px; height: 58px; border-radius: 50%; background: var(--sun);
    margin: 0 auto 16px;
  }
  .brand__name { font-size: 46px; line-height: 48px; letter-spacing: 1px; }
  .brand__tag { font-size: 25px; line-height: 32px; letter-spacing: 1px; }
</style>
</head>
<body>

<section class="card card--front">
  <div class="front__accent" aria-hidden="true"></div>

  <div class="doctors">
    <p><span class="given">Mei-Ran</span> <span class="family">Tsai</span><span class="degree">, DMD</span></p>
    <p><span class="given">Corinne</span> <span class="family">Walbeck</span><span class="degree">, DMD</span></p>
  </div>

  <div class="practice">
    <p class="practice__name">Maplebrook Pediatric Dentistry</p>
    <p class="practice__address">482 Quarry Lane&nbsp; Suite</p>
    <p class="practice__address">517 Fernhollow, PA 17521</p>
  </div>

  <ul class="contacts">
    <li>717.555.0193
      <svg class="icon-fill" viewBox="0 0 24 24" aria-hidden="true"><path d="M6.6 10.8a15.1 15.1 0 0 0 6.6 6.6l2.2-2.2a1 1 0 0 1 1-.25 11.4 11.4 0 0 0 3.6.57 1 1 0 0 1 1 1V20a1 1 0 0 1-1 1A17 17 0 0 1 3 4a1 1 0 0 1 1-1h3.5a1 1 0 0 1 1 1c0 1.25.2 2.45.57 3.57a1 1 0 0 1-.25 1z"/></svg>
    </li>
    <li>Mei-ran@maplebrookkidsdental.example
      <svg class="icon-mail" viewBox="0 0 24 24" aria-hidden="true"><rect x="1" y="4" width="22" height="16"/><path d="M2 5l10 7 10-7"/></svg>
    </li>
    <li>Corinne@maplebrookkidsdental.example
      <svg class="icon-mail" viewBox="0 0 24 24" aria-hidden="true"><rect x="1" y="4" width="22" height="16"/><path d="M2 5l10 7 10-7"/></svg>
    </li>
    <li>www.maplebrookkidsdental.example
      <svg class="icon-fill" viewBox="0 0 24 24" aria-hidden="true"><circle cx="12" cy="12" r="11"/></svg>
    </li>
  </ul>
</section>

<section class="card card--back">
  <div class="brand">
    <div class="brand__mark" aria-hidden="true"></div>
    <p class="brand__name">maplebrook</p>
    <p class="brand__tag">pediatric dentistry</p>
  </div>
</section>

</body>
</html>
```